Redesign of business card for Cedar Ridge Mechanical

We are looking for a new design for our business cards for Cedar Ridge Mechanical. We are a plumbing & HVAC construction company, operating on the West Coast of Canada and USA. Logo attached.
Industry/Entity Type
Construction - Plumbing & HVAC
Contact Information for Business Card
Name, address, phone numbers, email, website address
Look and feel
Each slider illustrates characteristics of the customer's brand and the style your logo design should communicate.

```html
<!DOCTYPE html>
<html lang="en">
<head>
<meta charset="utf-8">
<title>Cedar Ridge Mechanical – Business Card</title>
<link href="https://fonts.googleapis.com/css2?family=Poppins:wght@300;400;700&display=swap" rel="stylesheet">
<style>
  :root {
    --backdrop: #232324;
    --card: #1d1d1f;
    --card-edge: #ececec;
    --ink: #ffffff;
    --ink-soft: #e6e6e6;
    --pattern-a: #2a2a2c;
    --pattern-b: #1a1a1b;
  }
  * { margin: 0; padding: 0; box-sizing: border-box; }
  html, body { width: 1200px; height: 711px; overflow: hidden; }
  body {
    background: var(--backdrop);
    font-family: "Poppins", sans-serif;
    color: var(--ink);
    position: relative;
  }
  .card {
    position: absolute;
    top: 200px;
    width: 540px;
    height: 310px;
    background: var(--card);
    border-radius: 26px;
    border: 2px solid var(--card-edge);
    overflow: hidden;
  }
  .card--front { left: 40px; }
  .card--back { left: 620px; }

  .front-pattern {
    position: absolute;
    inset: 0;
    background: radial-gradient(ellipse at 60% 40%, var(--pattern-a), var(--pattern-b));
  }
  .front-brand {
    position: absolute;
    inset: 0;
    display: flex;
    align-items: center;
    justify-content: center;
    gap: 14px;
  }
  .brand-square {
    width: 22px;
    height: 22px;
    background: var(--ink);
    flex: none;
  }
  .brand-name {
    font-weight: 700;
    font-size: 28px;
    letter-spacing: 0.5px;
    color: var(--ink);
  }

  .back-brand {
    position: absolute;
    top: 34px;
    right: 30px;
    display: flex;
    align-items: center;
    gap: 12px;
  }
  .back-brand .brand-square { width: 20px; height: 20px; }
  .back-brand .brand-name { font-size: 25px; }

  .divider {
    position: absolute;
    left: 250px;
    right: 0;
    top: 158px;
    height: 2px;
    background: var(--ink);
  }
  .person {
    position: absolute;
    left: 30px;
    top: 118px;
  }
  .person-name { font-size: 30px; line-height: 1.2; white-space: nowrap; }
  .person-name .first { font-weight: 700; }
  .person-name .last { font-weight: 300; }
  .person-role { font-size: 15px; font-weight: 400; color: var(--ink-soft); margin-top: 6px; }

  .contact {
    position: absolute;
    right: 26px;
    top: 170px;
    text-align: right;
    font-weight: 300;
    font-size: 13px;
    line-height: 1.4;
    color: var(--ink-soft);
  }
  .contact-address { margin-bottom: 6px; }
  .contact-line { display: flex; align-items: center; justify-content: flex-end; gap: 8px; }
  .contact-line svg { width: 12px; height: 12px; flex: none; }
  .contact-plain { padding-right: 20px; }
</style>
</head>
<body>
  <section class="card card--front">
    <div class="front-pattern" role="img" aria-label="Repeating brand pattern background"></div>
    <div class="front-brand">
      <span class="brand-square"></span>
      <span class="brand-name">Cedar Ridge Mechanical</span>
    </div>
  </section>

  <section class="card card--back">
    <div class="back-brand">
      <span class="brand-square"></span>
      <span class="brand-name">Cedar Ridge Mechanical</span>
    </div>
    <div class="divider"></div>
    <div class="person">
      <p class="person-name"><span class="first">Marta</span> <span class="last">Kovalenko</span></p>
      <p class="person-role">Founder &amp; CEO</p>
    </div>
    <div class="contact">
      <p class="contact-address">1840 Harbor Line Rd. Suite 110<br>Tacoma, WA 98402</p>
      <p class="contact-line">(253) 555-0174
        <svg viewBox="0 0 24 24" fill="#fff"><path d="M6.6 10.8a15 15 0 0 0 6.6 6.6l2.2-2.2a1 1 0 0 1 1-.25 11.4 11.4 0 0 0 3.6.6 1 1 0 0 1 1 1V20a1 1 0 0 1-1 1A17 17 0 0 1 3 4a1 1 0 0 1 1-1h3.5a1 1 0 0 1 1 1c0 1.2.2 2.4.6 3.6a1 1 0 0 1-.25 1z"/></svg>
      </p>
      <p class="contact-line">www.yourwebsite.com
        <svg viewBox="0 0 24 24" fill="none" stroke="#fff" stroke-width="2"><circle cx="12" cy="12" r="9"/><path d="M3 12h18M12 3a14 14 0 0 1 0 18M12 3a14 14 0 0 0 0 18"/></svg>
      </p>
      <p class="contact-line">info@yourwebsite.com
        <svg viewBox="0 0 24 24" fill="none" stroke="#fff" stroke-width="2"><rect x="3" y="5" width="18" height="14" rx="1"/><path d="M3 6l9 7 9-7"/></svg>
      </p>
      <p class="contact-plain">www.yourwebsite.com</p>
    </div>
  </section>
</body>
</html>
```